Verodex business card

Business card for sustainable investment company called "Verodex". Verodex is an exchange platform selling carbon credits between buyers and sellers. Carbon Credits are an environmental commodity for reducing global carbon emissions.

the card should obviously have our logo and the theme should be sustainability/environment mixed with a trading platform.

Contact Information for Business Card

Logo, Name, Title, Phone, Email

Colors
0054AA
0677BA
7BADD7
CADEEF
E8F1F8
0094D4
00A9DD
6FCCEA
C7EBF8
E9F6FB
00AB8E
00BBA5
67D7C9
C6EFE9
E9F9F6
59FF00
82FF00
B8FF75
E3FFCB
F4FFEA

```html
<!DOCTYPE html>
<html lang="en">
<head>
<meta charset="UTF-8">
<title>Verodex Business Card</title>
<link rel="stylesheet" href="https://fonts.googleapis.com/css2?family=Open+Sans:wght@400;600;700;800&display=swap">
<style>
  :root {
    --stage: #333333;
    --front-light: #68cedc;
    --front-mid: #5aa6d0;
    --front-deep: #4a78c0;
    --mark-tone: #4d8cc8;
    --back-navy: #142a52;
    --name-cyan: #5fc3dc;
    --brand-blue: #5aa4d6;
    --text-white: #ffffff;
    --icon-blue: #6cb8e4;
    --divider: #b9c6dc;
  }
  * { margin: 0; padding: 0; box-sizing: border-box; }
  html, body {
    width: 1200px; height: 780px; overflow: hidden;
    background: var(--stage);
    font-family: "Open Sans", Arial, sans-serif;
  }
  .stage {
    position: relative; width: 1200px; height: 780px;
    display: flex; align-items: center; justify-content: center; gap: 50px;
  }
  .card {
    position: relative; width: 525px; height: 300px; overflow: hidden;
  }
  /* Front face */
  .card--front {
    background: linear-gradient(35deg, var(--front-light) 0%, var(--front-mid) 55%, var(--front-deep) 100%);
    display: flex; align-items: center; justify-content: center; gap: 14px;
  }
  .front-brand__dot {
    width: 30px; height: 30px; border-radius: 50%;
    background: var(--mark-tone);
  }
  .front-brand__name {
    font-weight: 700; font-size: 46px; letter-spacing: 4px;
    text-transform: uppercase; color: var(--mark-tone);
  }
  /* Back face */
  .card--back {
    background: var(--back-navy);
    display: flex;
  }
  .back-brand {
    width: 52%; display: flex; align-items: center; justify-content: center; gap: 12px;
  }
  .back-brand__dot {
    width: 28px; height: 28px; border-radius: 50%; background: var(--brand-blue);
  }
  .back-brand__name {
    font-weight: 700; font-size: 40px; color: var(--brand-blue);
  }
  .back-divider {
    width: 1px; align-self: center; height: 58%;
    background: var(--divider);
  }
  .contact {
    flex: 1; padding: 0 0 0 26px;
    display: flex; flex-direction: column; justify-content: center;
    color: var(--text-white);
  }
  .contact__name {
    font-weight: 800; font-size: 24px; color: var(--name-cyan); line-height: 1.1;
  }
  .contact__title {
    font-weight: 700; font-size: 13px; margin-top: 2px;
  }
  .contact__address {
    font-size: 12.5px; line-height: 1.35; margin-top: 12px;
  }
  .contact__list { list-style: none; margin-top: 10px; }
  .contact__item {
    display: flex; align-items: center; gap: 8px;
    font-size: 12.5px; line-height: 1.55;
  }
  .contact__icon { width: 13px; height: 13px; flex: none; }
</style>
</head>
<body>
<main class="stage">
  <section class="card card--front" aria-label="Card front">
    <span class="front-brand__dot"></span>
    <span class="front-brand__name">Verodex</span>
  </section>

  <section class="card card--back" aria-label="Card back">
    <div class="back-brand">
      <span class="back-brand__dot"></span>
      <span class="back-brand__name">Verodex</span>
    </div>
    <div class="back-divider"></div>
    <div class="contact">
      <h1 class="contact__name">Marta Kolarova</h1>
      <p class="contact__title">Managing Director</p>
      <p class="contact__address">418 Linden Ave. Suite 300<br>Austin, TX 78701</p>
      <ul class="contact__list">
        <li class="contact__item">
          <svg class="contact__icon" viewBox="0 0 24 24" fill="var(--icon-blue)"><path d="M6.6 10.8a15.1 15.1 0 0 0 6.6 6.6l2.2-2.2c.3-.3.7-.4 1-.2 1.1.4 2.3.6 3.6.6.6 0 1 .4 1 1V20c0 .6-.4 1-1 1A17 17 0 0 1 3 4c0-.6.4-1 1-1h3.5c.6 0 1 .4 1 1 0 1.3.2 2.5.6 3.6.1.3 0 .7-.2 1z"/></svg>
          <span>(512) 555-0147</span>
        </li>
        <li class="contact__item">
          <svg class="contact__icon" viewBox="0 0 24 24" fill="none" stroke="var(--icon-blue)" stroke-width="2"><rect x="3" y="5" width="18" height="14" rx="1"/><path d="M3 6l9 7 9-7"/></svg>
          <span>info@website.com</span>
        </li>
        <li class="contact__item">
          <svg class="contact__icon" viewBox="0 0 24 24" fill="none" stroke="var(--icon-blue)" stroke-width="2"><circle cx="12" cy="12" r="9"/><path d="M3 12h18M12 3c3 3 3 15 0 18M12 3c-3 3-3 15 0 18"/></svg>
          <span>www.website.com</span>
        </li>
      </ul>
    </div>
  </section>
</main>
</body>
</html>
```